Investment Management Firm Power point template

Marrow Holdings is a real estate investment firm focused on buying commercial office and residential property in the UK. We produce powerpoint presentations for our Board of Directors, Investment Committee and also to external investors.

We are looking for a powerpoint design template which we can use for future presentations which provide a professional look and feel.

Our current website: http://www.marrowholdings.example.co.uk/

Target Market(s)

Institution Investors, Board of Directors, Professionals

Industry/Entity Type

Real Estate

Requirements
Must have
• Leverage off the current logo and colour scheme. However, does not have to purely rely on this colour scheme.
• - Title page
• - Content Page
• - Slide where graphs can be incorporated
• - Slide where photos can be incorporated
• - Slide of UK Map which can show where the property portfolio is currently located
• - Other slides incorporating smart art or other designs that can be used for future presentations
Nice to have
• An example of graphics that we would love to have in the powerpoint pack which we can easily edit has been attached

```html
<!DOCTYPE html>
<html lang="en">
<head>
<meta charset="utf-8">
<title>Marrow Holdings – Chart Slide</title>
<link rel="stylesheet" href="https://fonts.googleapis.com/css2?family=Titillium+Web:wght@400;600;700&family=Roboto:wght@700;900&display=swap">
<style>
  :root {
    --brand-blue: #1d5786;
    --footer-blue: #296a96;
    --ink: #1f2a33;
    --body-text: #4a4f55;
    --slice-light: #41acd4;
    --slice-navy: #14507a;
    --slice-charcoal: #373737;
    --slice-teal: #358fad;
    --white: #ffffff;
  }
  html, body {
    margin: 0;
    padding: 0;
    width: 1200px;
    height: 900px;
    overflow: hidden;
  }
  .slide {
    position: relative;
    width: 1200px;
    height: 900px;
    overflow: hidden;
    font-family: "Titillium Web", sans-serif;
    background: var(--white);
  }
  .slide-backdrop {
    position: absolute;
    inset: 0 0 57px 0;
    background: linear-gradient(135deg, #f7f8f9 0%, #f1f3f5 45%, #e9ecef 75%, #f4f5f7 100%);
  }
  .slide-title {
    position: absolute;
    left: 24px;
    top: 26px;
    margin: 0;
    font-size: 33px;
    font-weight: 700;
    color: var(--ink);
    line-height: 1.2;
  }
  .slide-title .accent { color: var(--brand-blue); }
  .title-rule {
    position: absolute;
    left: 22px;
    top: 68px;
    width: 238px;
    height: 3px;
    background: var(--brand-blue);
  }
  .content {
    position: absolute;
    left: 81px;
    top: 176px;
    width: 530px;
  }
  .content-subtitle {
    margin: 0 0 4px;
    font-size: 24px;
    font-weight: 700;
    color: var(--brand-blue);
  }
  .content p {
    margin: 0 0 30px;
    font-size: 18.5px;
    line-height: 30px;
    color: var(--body-text);
  }
  .content .emphasis {
    font-weight: 700;
    color: var(--brand-blue);
  }
  .pie-chart {
    position: absolute;
    left: 0;
    top: 0;
  }
  .pie-label {
    font-family: "Roboto", sans-serif;
    font-weight: 900;
    font-size: 39px;
    fill: var(--white);
    text-anchor: middle;
    dominant-baseline: middle;
  }
  .footer {
    position: absolute;
    left: 0;
    bottom: 0;
    width: 1200px;
    height: 57px;
  }
  .footer-band {
    position: absolute;
    left: 0;
    top: 0;
    width: 915px;
    height: 57px;
    background: var(--footer-blue);
  }
  .copyright {
    position: absolute;
    left: 20px;
    top: 0;
    line-height: 57px;
    font-size: 20px;
    color: var(--white);
  }
  .brand-box {
    position: absolute;
    left: 921px;
    top: 2px;
    width: 271px;
    height: 50px;
    border: 2px solid var(--footer-blue);
    background: var(--white);
    display: flex;
    align-items: center;
    justify-content: center;
    gap: 14px;
  }
  .brand-mark {
    width: 24px;
    height: 24px;
    background: var(--brand-blue);
  }
  .brand-name {
    font-size: 27px;
    font-weight: 600;
    color: var(--brand-blue);
  }
</style>
</head>
<body>
<main class="slide">
  <div class="slide-backdrop" role="img" aria-label="Faint background photograph of a modern glass office building"></div>

  <h1 class="slide-title"><span class="accent">Slide</span> Title Here</h1>
  <div class="title-rule"></div>

  <section class="content">
    <h2 class="content-subtitle">Subtitle Here</h2>
    <p>Lorem ipsum dolor sit amet, consectetur adipiscing elit, sed do eiusmod tempor incididunt ut labore et dolore magna aliqua. Ut enim ad minim <span class="emphasis">veniam, quis nostrud exercitation. Lorem ipsum dolor sit amet.</span></p>
    <p>Consectetur adipiscing elit, sed do eiusmod tempor incididunt ut labore et dolore magna aliqua. Ut enim ad minim veniam, quis nostrud exercitation.</p>
    <p>Consectetur adipiscing elit, sed do eiusmod tempor incididunt ut labore et dolore magna aliqua. Ut enim ad minim veniam, quis nostrud exercitation.Consectetur adipiscing elit, sed do eiusmod tempor incididunt ut labore et dolore magna aliqua. Ut enim ad minim veniam, quis nostrud exercitation.</p>
  </section>

  <svg class="pie-chart" width="1200" height="900" viewBox="0 0 1200 900" aria-label="Pie chart: 10%, 31%, 30%, 29%">
    <g stroke="#ffffff" stroke-width="2" stroke-linejoin="round">
      <path d="M914 450 L914 216 A234 234 0 0 1 1079.5 284.5 Z" fill="var(--slice-light)"/>
      <path d="M914 450 L1079.5 284.5 A234 234 0 0 1 1027.4 654.7 Z" fill="var(--slice-navy)"/>
      <path d="M914 450 L1027.4 654.7 A234 234 0 0 1 694.1 530 Z" fill="var(--slice-charcoal)"/>
      <path d="M914 450 L694.1 530 A234 234 0 0 1 914 216 Z" fill="var(--slice-teal)"/>
    </g>
    <text class="pie-label" x="976" y="306">10%</text>
    <text class="pie-label" x="1063" y="479">31%</text>
    <text class="pie-label" x="868" y="609">30%</text>
    <text class="pie-label" x="795" y="373">29%</text>
  </svg>

  <footer class="footer">
    <div class="footer-band"><span class="copyright">Copyright text here</span></div>
    <div class="brand-box">
      <span class="brand-mark"></span>
      <span class="brand-name">Marrow Holdings</span>
    </div>
  </footer>
</main>
</body>
</html>
```